Women's Uplift & Praise Luncheon - Matching Poster, flyer and Postcard

We are a Christian Event & Travel Company and we are hosting our inaugural event on June 10, 2017. This event is a Women's Uplift & Praise Luncheon aboard a private yacht leaving out of Crescent Landing, Maryland. The event will cater to women who have a vision to start or have already embarked on the journey of starting or growing a business or ministry. The event calls for a matching poster, flyer and postcard design that give an elegant & exquisite feel with just the right breath of freshness. The colors should reflect our logo as this is our launch event. I have also included 2 photos of the Islandsong Heritage Park production (one of our sponsors) - Please include but do not make it take over the design - this is to advertise the door prize. The final design will portray the branding of the company (Christian, travel, events, elegance, professional), the branding of the event (elegant and luxurious) and the importance of this launch event.
Please include the following information:
Lanternway Event & Travel Group presents
Event name: Rising Tide: Grace, Patience & Devotion.
Tag Line/Description: An Exquisite Women's Uplift & Praise Luncheon.
Guest Speaker: Minister Harriet L. Dunmore (Photo included)
VP of Pinecrest Bank
Asst. Pastor & First Lady of Bethany Grove Baptist Church
Special Guest Psalmist: Minister Tasha Bellamy (Photo Included)
Worship Director of Stillmeadow Community Church
Vocalist, Songwriter, Musician, and Clinician
Venue: Aboard the Sovereign Pearl Yacht
Dock: Crescent Landing
512 Marlowe Quay, Fenwick, MD 20999
Boarding 10:00am
Sailing Promptly at 10:30am
(Please be on time the yacht will not wait)
Date: Saturday June 10, 2017
Tickets: Early Bird US$75.00/person (ends May 15, 2017)
Regular Tickets US$95.99
Purchase Tickets at www.lanternwayevent-travel.example/rising-tide
SPACE IS LIMITED DUE TO YACHT CAPACITY
Grand Prize: Vivienne Laroux Purse
Door Prize: 2 Tickets to the Hawaiian Islandsong Heritage Park
Other prizes for special ladies in attendance.
Ladies are asked to dress in Elegant White Ensemble
Corporate Sponsors:
The Islandsong Heritage Park (Logo included)
J. Ramsey Photography (Logo included)
Special Thanks to our Individual Sponsors:
Mrs. L. Garner, Mr. R Fielding & Mr. T. Ogden

Target Market(s)

Women, Business, Ministry, Christians, Middle to Upper Class

Industry/Entity Type

Events

Font styles to use
Serif
Script

Requirements
Must have
• Elegance, professional, vivid in color & font. be creative in Visual and FONT!
• Poster: 18" X 24"
• Flyer: one sided.
• ***** the final design chosen will have a cross referenced design of 1 flyer, 1 postcard 1 poster. This was included so you have a reference - Be creative!!!!!!
Nice to have
• Matching across all 3 designs (poster, flyer & postcard) but sized appropriately and just enough difference to play up the design and be appealing.
• I uploaded 3 example flyers to give you inspiration of the type of visuals I'm looking for. I removed my amateur sample because the designs were copying it instead of being creative.
Should not have
• Any thing inappropriate, alcohol oriented or sexual

```html
<!DOCTYPE html>
<html lang="en">
<head>
<meta charset="utf-8">
<title>Rising Tide – Women's Uplift &amp; Praise Luncheon</title>
<link rel="stylesheet" href="https://fonts.googleapis.com/css2?family=Cinzel:wght@400;600;700&family=Great+Vibes&family=Oswald:wght@400;500;600&family=Playfair+Display:wght@900&family=Roboto:wght@400;500&family=Pinyon+Script&display=swap">
<style>
:root{
  --ink:#000;
  --gold:#f3b531;
  --gold-light:#ffe27a;
  --gold-dark:#b5700f;
  --sky:#8fd0ec;
  --pink:#e55ad8;
  --navy:#1b2467;
  --yellow:#f3c21a;
  --paper:#ffffff;
  --text-dark:#1a1a1a;
  --arrow:#6a1a78;
}
*{box-sizing:border-box;margin:0;padding:0}
html,body{width:900px;height:1200px;overflow:hidden;background:var(--ink)}
p,h1{line-height:1.2}
.poster{position:relative;width:900px;height:1200px;overflow:hidden;
  background:
    radial-gradient(ellipse 470px 250px at 400px 200px, rgba(0,0,0,0) 55%, rgba(226,60,40,.75) 68%, rgba(120,20,80,.5) 82%, rgba(0,0,0,0) 100%),
    radial-gradient(ellipse 620px 320px at 420px 170px, rgba(90,18,70,.6), rgba(0,0,0,0) 85%),
    var(--ink);
  font-family:'Roboto',sans-serif;color:#fff}
.abs{position:absolute}

/* speaker portraits placeholder */
.speakers-photo{left:104px;top:0;width:396px;height:340px;
  -webkit-mask-image:linear-gradient(180deg,#000 70%,rgba(0,0,0,0) 100%);
          mask-image:linear-gradient(180deg,#000 70%,rgba(0,0,0,0) 100%)}
.speakers-photo .portrait-left{position:absolute;left:0;top:20px;width:200px;height:320px;border-radius:90px 90px 0 0;
  background:linear-gradient(180deg,#2a1a14 0%,#5a3526 35%,#c9b8a4 62%,#eee6da 100%)}
.speakers-photo .portrait-right{position:absolute;left:150px;top:40px;width:246px;height:300px;border-radius:100px 100px 0 0;
  background:linear-gradient(180deg,#1e1210 0%,#7a4634 32%,#c2282b 58%,#b01e24 100%)}

.brand-box{left:611px;top:72px;width:211px;height:142px;background:var(--navy);
  display:flex;flex-direction:column;align-items:center;justify-content:center;gap:10px}
.brand-box .dot{width:18px;height:18px;border-radius:50%;background:var(--gold)}
.brand-box .name{font-family:'Cinzel',serif;font-weight:600;font-size:17px;line-height:1.25;color:var(--gold);text-align:center}

.title{left:0;width:900px;top:334px;text-align:center;font-family:'Cinzel',serif;font-weight:700;font-size:100px;line-height:1;letter-spacing:2px;
  background:linear-gradient(180deg,var(--gold-light) 15%,var(--gold) 50%,var(--gold-dark) 85%);
  -webkit-background-clip:text;background-clip:text;color:transparent}
.subtitle{left:0;width:900px;top:424px;text-align:center;font-family:'Great Vibes',cursive;font-size:66px;line-height:1;color:var(--sky)}
.tagline{left:0;width:900px;top:496px;text-align:center;font-family:'Cinzel',serif;font-size:19px;letter-spacing:1px;color:#fff}

.speaker{font-size:21px;color:var(--pink)}
.speaker-sub{font-size:14px;color:var(--pink)}
.psalmist{font-size:19px;color:#fff}
.psalmist .name{color:var(--gold-light)}
.psalmist-sub{font-size:13px;color:var(--gold-light);text-align:center;line-height:1.45}

.fire-photo{left:530px;top:534px;width:370px;height:194px;
  background:radial-gradient(ellipse at 50% 55%, #e08a22 0%, #5a2a10 45%, #0c0808 85%)}
.info-band{left:0;top:708px;width:900px;height:312px}
.dance-photo{left:576px;top:728px;width:324px;height:292px;
  background:linear-gradient(160deg,#3a3222 0%,#6d5a2c 45%,#c9a85a 70%,#2d3a1e 100%)}

.venue{left:0;width:570px;text-align:center;color:#e6d6ec;font-size:16.5px}
.date{left:26px;top:850px;font-family:'Playfair Display',serif;font-weight:900;font-size:50px;line-height:1.1;color:var(--gold);
  font-variant-numeric:lining-nums;transform:scaleX(.88);transform-origin:left}
.ticket{left:26px;font-family:'Oswald',sans-serif;font-weight:500;font-size:20px;color:#fff}
.ticket .hl{color:var(--gold)}

.sheet{left:0;top:1020px;width:900px;height:180px;background:var(--paper)}
.sponsors-tab{left:712px;top:1018px;width:188px;height:24px;background:var(--ink);color:#fff;font-size:13.5px;font-weight:500;
  display:flex;align-items:center;padding-left:22px}
.limited{left:26px;top:1038px;font-family:'Oswald',sans-serif;font-weight:500;font-size:22px;color:var(--text-dark)}
.prize-tag{left:0;width:146px;height:23px;font-family:'Oswald',sans-serif;font-weight:600;font-size:17px;color:var(--text-dark);padding-left:26px;line-height:23px;
  background:var(--yellow);clip-path:polygon(0 0,88% 0,100% 50%,88% 100%,0 100%)}
.prize-text{left:158px;font-family:'Oswald',sans-serif;font-weight:600;font-size:17px;color:var(--text-dark)}
.note{left:26px;font-family:'Oswald',sans-serif;font-weight:400;font-size:17px;color:var(--text-dark)}
.note .script{font-family:'Pinyon Script',cursive;font-size:21px}
.sponsor-photo{left:608px;top:1064px;width:96px;height:68px;background:#f1f1f1;
  display:flex;align-items:center;justify-content:center;text-align:center;
  font-size:10px;color:#444;line-height:1.3}
.sponsor-park{left:712px;top:1078px;width:180px;display:flex;align-items:center;gap:8px}
.sponsor-park .dot{width:20px;height:20px;border-radius:50%;background:#d89a18;flex:none}
.sponsor-park .name{font-weight:500;font-size:15px;color:#b07a10;line-height:1.15}
.thanks{left:610px;top:1144px;font-size:12.5px;color:var(--text-dark);line-height:1.5}
</style>
</head>
<body>
<main class="poster">
  <div class="abs speakers-photo" role="img" aria-label="Portraits of the guest speaker in a red jacket and the special guest psalmist in a white dress">
    <div class="portrait-left"></div>
    <div class="portrait-right"></div>
  </div>

  <div class="abs brand-box">
    <span class="dot"></span>
    <span class="name">Lanternway Event<br>&amp; Travel Group</span>
  </div>

  <h1 class="abs title">Rising Tide</h1>
  <p class="abs subtitle">Grace, Patience &amp; Devotion.</p>
  <p class="abs tagline">An Exquisite Women's Uplift &amp; Praise Luncheon.</p>

  <p class="abs speaker" style="left:31px;top:558px">Guest Speaker: Minister Harriet L. Dunmore</p>
  <p class="abs speaker-sub" style="left:27px;top:587px">VP of Pinecrest Bank, Asst. Pastor &amp; First Lady of Bethany Grove Baptist Church</p>
  <p class="abs psalmist" style="left:90px;top:624px">Special Guest Psalmist: <span class="name">Minister Tasha Bellamy</span></p>
  <p class="abs psalmist-sub" style="left:60px;width:440px;top:650px">Worship Director of Stillmeadow Community Church Vocalist,<br>Songwriter, Musician, and Clinician</p>

  <div class="abs fire-photo" role="img" aria-label="Night performance of fire knife dancers"></div>

  <svg class="abs info-band" viewBox="0 0 900 312" aria-hidden="true">
    <defs>
      <linearGradient id="bandFill" x1="0" y1="0" x2="0" y2="1">
        <stop offset="0" stop-color="#5a0c48"/>
        <stop offset="1" stop-color="#3a0630"/>
      </linearGradient>
    </defs>
    <polygon points="0,0 572,0 592,20 900,20 900,312 0,312" fill="url(#bandFill)"/>
    <polygon points="572,0 592,20 900,20 900,24 590,24 570,4" fill="#7a1a66"/>
  </svg>

  <div class="abs dance-photo" role="img" aria-label="Polynesian dancers in grass skirts performing on stage"></div>

  <p class="abs venue" style="top:732px">Venue: Aboard the Sovereign Pearl Yacht</p>
  <p class="abs venue" style="top:756px">Dock: Crescent Landing, 512 Marlowe Quay, Fenwick, MD 20999</p>
  <p class="abs venue" style="top:786px;font-size:18.5px">Boarding 10:00am &nbsp;|&nbsp; Sailing Promptly at 10:30am</p>
  <p class="abs venue" style="top:813px;font-size:14px">(Please be on time the yacht will not wait)</p>

  <p class="abs date">SATURDAY JUNE 10, 2017</p>

  <p class="abs ticket" style="top:915px">Tickets : Early Bird <span class="hl">US$75.00/person</span> (ends May 15, 2017)</p>
  <p class="abs ticket" style="top:947px">Regular Tickets <span class="hl">US$95.99</span></p>
  <p class="abs ticket" style="top:979px;font-size:19px">Purchase Tickets at <span class="hl">www.lanternwayevent-travel.example/rising-tide</span></p>

  <div class="abs sheet"></div>
  <div class="abs sponsors-tab">Corporate Sponsors</div>

  <svg class="abs" style="left:0;top:0;width:900px;height:1200px;pointer-events:none" viewBox="0 0 900 1200" aria-hidden="true">
    <path d="M506 1110 C 590 1080, 630 1030, 636 985" fill="none" stroke="var(--arrow)" stroke-width="6" stroke-linecap="round"/>
    <polygon points="606,990 644,962 652,1002" fill="var(--arrow)"/>
  </svg>

  <p class="abs limited">SPACE IS LIMITED DUE TO YACHT CAPACITY</p>

  <div class="abs prize-tag" style="top:1076px">Grand Prize</div>
  <p class="abs prize-text" style="top:1075px">Vivienne Laroux Purse</p>
  <div class="abs prize-tag" style="top:1106px">Door Prize</div>
  <p class="abs prize-text" style="top:1105px">2 Tickets to the Hawaiian Islandsong Heritage Park</p>

  <p class="abs note" style="top:1134px">Other prizes for special ladies in attendance.</p>
  <p class="abs note" style="top:1158px">Ladies are asked to dress in <span class="script">Elegant White Ensemble</span></p>

  <div class="abs sponsor-photo">J. Ramsey<br>Photography</div>
  <div class="abs sponsor-park">
    <span class="dot"></span>
    <span class="name">Islandsong<br>Heritage Park</span>
  </div>

  <p class="abs thanks">Special Thanks to our Individual Sponsors:<br>Mrs. L. Garner, Mr. R Fielding &amp; Mr. T. Ogden</p>
</main>
</body>
</html>
```